Sell the dream! Property investment proposal document

We are looking for a proposal document which outlines our vision for property development. The purpose of the document is to raise investment from investors - sell the dream!
Brief summary:
Kestrel Dwellings Developments, is an emerging New Zealand property investment company with a focus on providing unique property investment opportunities.
Our expertise and capabilities in architectural modular homes provide us with a remarkable advantage in tackling the development of properties that are typically considered challenging, remote, or uniquely positioned.
Our specialization in this niche sector of property development not only sets us apart from competitors, but also paves the way for lucrative investment opportunities in the New Zealand property market.
Feel free to use any images from www.kestreldwellings.co.nz
Target Market(s)
investors for a unique property development opportunity
Industry/Entity Type
luxury property development in unique locations throughout New Zealand
Colors
Designer to choose only greyscale colors for use in the design.
Look and feel

```html
<!DOCTYPE html>
<html lang="en">
<head>
<meta charset="utf-8">
<title>Kestrel Dwellings Developments – Investment Proposal</title>
<link rel="stylesheet" href="https://fonts.googleapis.com/css2?family=Montserrat:wght@300;400;500;600;700&display=swap">
<style>
:root{
  --ink:#1f1f1f;
  --paper:#ffffff;
  --stage:#d6d6d6;
  --pattern-a:#f4f4f4;
  --pattern-b:#e2e2e2;
  --muted:#cfcfcf;
  --rule:#8a8a8a;
}
*{box-sizing:border-box;margin:0;padding:0}
html,body{width:1200px;height:2400px;overflow:hidden;background:var(--stage)}
body{font-family:"Montserrat",sans-serif;color:var(--paper);position:relative}
.spread{position:absolute;left:45px;width:1110px;height:394px;background:var(--ink);overflow:hidden;box-shadow:0 4px 10px rgba(0,0,0,.18)}
.spread--cover{top:304px}
.spread--intro{top:1002px}
.spread--value{top:1700px}
.abs{position:absolute}
.pattern{position:absolute;background:linear-gradient(135deg,var(--pattern-a),var(--pattern-b) 50%,var(--pattern-a))}
.photo{position:absolute}
.frame{position:absolute;border:1px solid var(--paper)}
.page-title{position:absolute;left:29px;top:32px;line-height:1}
.page-title .kicker{display:block;font-weight:400;font-size:17px;letter-spacing:5px}
.page-title .headline{display:block;font-weight:600;font-size:30px;margin-top:3px;letter-spacing:.3px}
.page-title--right{left:582px}
.body-copy{position:absolute;font-size:6.6px;line-height:1.32;color:var(--muted)}
.body-copy p{margin-bottom:8px}
.body-copy strong{color:var(--paper);font-weight:700;font-size:7.4px}
.footer{position:absolute;top:356px;height:10px;display:flex;align-items:center;font-size:7.5px;letter-spacing:.4px}
.footer .rule{flex:1;height:1px;background:var(--paper);margin:0 3px 0 4px}
.footer .folio{width:9px;height:9px;border-radius:50%;background:var(--paper);color:var(--ink);font-size:6px;font-weight:700;display:flex;align-items:center;justify-content:center}
.wordmark{position:absolute;font-weight:400;color:var(--paper);line-height:1}
.contact{position:absolute;left:300px;width:210px;top:92px;text-align:center;font-size:11.5px}
.contact .item{margin-bottom:16px}
.contact .icon{display:block;margin:0 auto 4px;width:20px;height:20px}
.contact .follow{font-size:9px;letter-spacing:2.5px;margin-top:6px}
.contact .dots{display:flex;justify-content:center;gap:4px;margin-top:5px}
.contact .dots span{width:10px;height:10px;border-radius:50%;background:var(--paper)}
.cover-title{position:absolute;left:707px;top:284px;font-weight:700;font-size:19px;letter-spacing:.2px}
.cover-sub{position:absolute;left:707px;top:303px;font-size:11px;letter-spacing:4.2px}
.cover-tag{position:absolute;left:691px;top:318px;width:261px;height:17px;background:var(--paper);color:var(--ink);font-size:12.5px;font-weight:500;letter-spacing:4px;padding-left:16px;line-height:17px}
.cover-web{position:absolute;left:707px;top:355px;font-size:11px;letter-spacing:3px}
.cover-web b{font-weight:700}
.label{position:absolute;background:var(--paper);color:var(--ink);font-weight:700;font-size:8.6px;padding:1px 8px}
.lead{position:absolute;font-weight:700;font-size:8.2px;line-height:1.2}
.feature{position:absolute;left:270px;width:249px;display:flex;gap:12px;font-size:6.6px;line-height:1.3;color:var(--muted)}
.feature svg{flex:none;width:22px;height:22px}
.feature--ruled::after{content:"";position:absolute;left:36px;right:0;bottom:-10px;border-bottom:1px dashed var(--rule)}
.highlight{background:var(--paper);color:var(--ink);padding:0 8px;margin-right:6px}
</style>
</head>
<body>

<!-- Spread: back cover & front cover -->
<section class="spread spread--cover">
  <div class="pattern" style="left:0;top:0;width:45px;height:394px" role="img" aria-label="Light grey geometric line pattern"></div>
  <div class="frame" style="left:36px;top:39px;width:223px;height:318px"></div>
  <div class="photo" style="left:31px;top:54px;width:215px;height:288px;background:linear-gradient(180deg,#4a4a46 0%,#8a8780 40%,#6c645a 70%,#2d2b29 100%)" role="img" aria-label="Glass-walled living room with armchair looking out to rocky mountains"></div>

  <div class="wordmark" style="left:300px;width:210px;text-align:center;top:36px;font-size:30px">Kestrel</div>
  <div class="contact">
    <div class="item">
      <svg class="icon" viewBox="0 0 20 20"><circle cx="10" cy="10" r="10" fill="#fff"/><path d="M7 5.5l2 2-1 1.5c.8 1.5 1.6 2.3 3 3l1.5-1 2 2-1.3 1.7c-3.4-.4-6.9-3.9-7.3-7.3z" fill="#1f1f1f"/></svg>
      09 412 6630
    </div>
    <div class="item">
      <svg class="icon" viewBox="0 0 20 20"><circle cx="10" cy="10" r="10" fill="#fff"/><path d="M10 4a4 4 0 0 1 4 4c0 3-4 8-4 8s-4-5-4-8a4 4 0 0 1 4-4z" fill="#1f1f1f"/><circle cx="10" cy="8" r="1.6" fill="#fff"/></svg>
      Tawhiri Flats, Auckland
    </div>
    <div class="item">
      <svg class="icon" viewBox="0 0 20 20"><circle cx="10" cy="10" r="10" fill="#fff"/><rect x="5" y="6.5" width="10" height="7" fill="none" stroke="#1f1f1f" stroke-width="1.3"/><path d="M5 6.5l5 4 5-4" fill="none" stroke="#1f1f1f" stroke-width="1.3"/></svg>
      sales@kestreldwellings.co.nz
    </div>
    <div class="item">
      <svg class="icon" viewBox="0 0 20 20"><circle cx="10" cy="10" r="10" fill="#fff"/><g fill="none" stroke="#1f1f1f" stroke-width="1.1"><circle cx="10" cy="10" r="5"/><ellipse cx="10" cy="10" rx="2.2" ry="5"/><path d="M5 10h10"/></g></svg>
      www.kestreldwellings.co.nz
    </div>
    <div class="follow">FOLLOW US ON</div>
    <div class="dots"><span></span><span></span></div>
  </div>

  <div class="pattern" style="left:555px;top:0;width:135px;height:394px" role="img" aria-label="Light grey geometric line pattern"></div>
  <div class="wordmark" style="right:31px;top:28px;font-size:46px">Kestrel</div>
  <div class="frame" style="left:629px;top:89px;width:448px;height:175px"></div>
  <div class="photo" style="left:635px;top:96px;width:425px;height:158px;background:linear-gradient(180deg,#d9dcdf 0%,#b9bdbf 35%,#5f6358 60%,#3f4138 80%,#6a6a56 100%)" role="img" aria-label="Long modular home in golden grassland under large trees"></div>
  <div class="cover-title">KESTREL DWELLINGS DEVELOPMENTS</div>
  <div class="cover-sub">AN EMERGING NEW ZEALAND PROPERTY</div>
  <div class="cover-tag">INVESTMENT COMPANY</div>
  <div class="cover-web">www.<b>kestreldwellings</b>.co.nz</div>
</section>

<!-- Spread: overview & origins -->
<section class="spread spread--intro">
  <h2 class="page-title"><span class="kicker">BUSINESS</span><span class="headline">OVERVIEW</span></h2>
  <div class="pattern" style="left:0;top:99px;width:59px;height:295px" role="img" aria-label="Light grey geometric line pattern"></div>
  <div class="frame" style="left:26px;top:99px;width:194px;height:247px"></div>
  <div class="photo" style="left:33px;top:112px;width:173px;height:220px;background:linear-gradient(180deg,#6f6f6c 0%,#c9b9a0 40%,#8f8878 60%,#4a4540 80%,#2f2c29 100%)" role="img" aria-label="Cantilevered glass pavilion on a coastal gravel site at dusk"></div>

  <div class="label" style="left:270px;top:34px">Kestrel Dwellings Developments</div>
  <p class="lead" style="left:270px;top:53px;width:240px">Is an emerging New Zealand property investment company with a focus on providing unique property investment opportunities.</p>

  <div class="feature feature--ruled" style="top:103px">
    <svg viewBox="0 0 22 22"><g fill="#fff"><circle cx="9" cy="8" r="3"/><path d="M3 17c0-3.5 2.7-6 6-6s6 2.5 6 6z"/><circle cx="17" cy="15" r="3.5"/></g><path d="M15.5 15l1.2 1.2 2-2.2" stroke="#1f1f1f" stroke-width="1.2" fill="none"/></svg>
    <span>Our expertise and capabilities in architectural modular homes provide us with a remarkable advantage in tackling the development of properties that are typically considered challenging, remote, or uniquely positioned.</span>
  </div>
  <div class="feature feature--ruled" style="top:155px">
    <svg viewBox="0 0 22 22"><g fill="#fff"><circle cx="5" cy="7" r="2"/><circle cx="11" cy="6" r="2.4"/><circle cx="17" cy="7" r="2"/><rect x="3" y="10" width="4" height="8"/><rect x="8.5" y="9.5" width="5" height="9"/><rect x="15" y="10" width="4" height="8"/></g></svg>
    <span>As a company, with 48 employees boasting a wealth of experience in handling complex architectural projects, making us well-equipped to navigate the intricacies and demands of such ventures.</span>
  </div>
  <div class="feature feature--ruled" style="top:205px">
    <svg viewBox="0 0 22 22"><g fill="#fff"><rect x="3" y="12" width="4" height="7"/><rect x="9" y="8" width="4" height="11"/><rect x="15" y="10" width="4" height="9"/><circle cx="11" cy="4" r="2"/></g></svg>
    <span>This advantage allows us to not only execute projects efficiently but also to deliver exceptional results within condensed time frames.</span>
  </div>
  <div class="feature feature--ruled" style="top:248px">
    <svg viewBox="0 0 22 22"><g fill="#fff"><path d="M8 4h6l-2 3h-2z"/><circle cx="11" cy="12" r="5"/><path d="M3 18h16v2H3z"/></g><path d="M11 9.5v5" stroke="#1f1f1f" stroke-width="1.2"/></svg>
    <span>By capitalizing on our ability to develop difficult, remote, or one-of-a-kind properties swiftly and effectively, Kestrel Dwellings Developments offers investors a rare chance to engage in projects that promise exceptional profitability in the New Zealand property market.</span>
  </div>
  <div class="feature" style="top:311px">
    <svg viewBox="0 0 22 22"><g fill="#fff"><circle cx="11" cy="9" r="6"/><path d="M7 14l-2 6 3-1.5 2 2 1-4zM15 14l2 6-3-1.5-2 2-1-4z"/></g><circle cx="11" cy="9" r="3" fill="#1f1f1f"/></svg>
    <span>Our specialization in this niche sector of property development not only sets us apart from competitors, but also paves the way for lucrative investment opportunities in the New Zealand property market.</span>
  </div>

  <div class="footer" style="left:62px;width:461px">www.kestreldwellings.co.nz<span class="rule"></span><span class="folio">1</span></div>

  <h2 class="page-title page-title--right"><span class="kicker">BUSINESS</span><span class="headline">ORIGINS</span></h2>
  <div class="body-copy" style="left:582px;top:99px;width:150px">
    <p>Kestrel Dwellings Developments was established with the goal of transforming the property investment market in New Zealand by introducing an innovative approach that centers on architectural modular designs and streamlined project timelines.</p>
    <p>Driven by our enthusiasm for architecture and real estate, we have expanded our successful business model to not only offer financial opportunities for investors but also to expand on our passion for high-end architectural design.</p>
    <p>With a wealth of experience accumulated over the past six years in the construction and the property market, we are pivoting to focus solely on our property development initiatives, presenting completed Kestrel projects to the market, in exclusive locations.</p>
    <p>These projects will boast high-quality standards, meticulous attention to detail and landscaping, and creative design elements.</p>
  </div>
  <div class="pattern" style="left:876px;top:34px;width:234px;height:251px" role="img" aria-label="Light grey geometric line pattern"></div>
  <div class="frame" style="left:755px;top:34px;width:245px;height:251px"></div>
  <div class="photo" style="left:773px;top:54px;width:319px;height:210px;background:linear-gradient(180deg,#c7ccd0 0%,#dfe2e3 35%,#7d8784 48%,#5e6a4c 62%,#a79a84 80%,#2a2a2a 100%)" role="img" aria-label="Minimal interior with floor lamp and floor-to-ceiling windows over green hills and a lake"></div>
  <div class="body-copy" style="left:582px;top:306px;width:500px">
    <p>By introducing completed Kestrel properties into the market, we aim to reach a wider audience, catering to individuals who prefer ready-to-occupy homes, over engaging in the design and construction process. This approach also simplifies the financing process for prospective buyers, as established properties are often preferred by financial lenders.</p>
  </div>
  <div class="footer" style="left:582px;width:504px">www.kestreldwellings.co.nz<span class="rule"></span><span class="folio">2</span></div>
</section>

<!-- Spread: advantage & financials -->
<section class="spread spread--value">
  <h2 class="page-title"><span class="kicker">COMPETITIVE</span><span class="headline">ADVANTAGE</span></h2>
  <div class="pattern" style="left:274px;top:0;width:281px;height:151px" role="img" aria-label="Light grey geometric line pattern"></div>
  <div class="frame" style="left:33px;top:92px;width:486px;height:190px;border-right:0;border-bottom-color:var(--rule)"></div>
  <div class="photo" style="left:48px;top:103px;width:230px;height:81px;background:linear-gradient(180deg,#3d3a30 0%,#6b5c3e 40%,#2a2823 70%,#5a5236 100%)" role="img" aria-label="Low dark home in a golden valley at sunset"></div>
  <div class="photo" style="left:285px;top:103px;width:232px;height:81px;background:linear-gradient(180deg,#f2f2f2 0%,#5a5a5a 35%,#2a2a2a 60%,#8a9296 80%,#4b5a3e 100%)" role="img" aria-label="Black cantilevered house over a coastal cliff"></div>
  <div class="photo" style="left:48px;top:191px;width:230px;height:79px;background:linear-gradient(180deg,#b8c0c2 0%,#4f6a42 40%,#1e1e1e 70%,#5b6e4a 100%)" role="img" aria-label="Black modular cabin surrounded by native bush"></div>
  <div class="photo" style="left:285px;top:191px;width:232px;height:79px;background:linear-gradient(180deg,#1f1f1f 0%,#5f8aa6 30%,#9ab6c4 55%,#b39f80 75%,#2b2b2b 100%)" role="img" aria-label="Lounge chairs before a wide window over a blue bay"></div>
  <div class="body-copy" style="left:33px;top:300px;width:520px">
    <p>Our competitive advantage lies in the uniqueness of our property investment opportunities. Unlike traditional real estate companies, we focus on offering properties that are not only profitable but also aesthetically pleasing and unique. By catering to the tastes of architecture lovers, we set ourselves apart from the competition and attract a niche market of customers who appreciate the artistry and design of our products.</p>
    <p>Additionally, the streamlined and condensed timelines facilitated by our modular approach provide quicker returns on investment.</p>
  </div>
  <div class="footer" style="left:29px;width:494px">www.kestreldwellings.co.nz<span class="rule"></span><span class="folio">3</span></div>

  <h2 class="page-title page-title--right"><span class="kicker">FINANCIAL</span><span class="headline">SUMMARY</span></h2>
  <div class="body-copy" style="left:582px;top:105px;width:190px">
    <p><strong>In terms of financial projections, with each development, we anticipate a profit of <span class="highlight">10%-20%</span>which will be project dependent.</strong></p>
    <p>This growth is fueled by the increasing demand for unique property investments in New Zealand and our ability to deliver high-quality services to the market in a condensed time frame, with heavily controlled costs.</p>
    <p>With a solid business model and a dedicated team, we are confident in our ability to achieve success and establish Kestrel Dwellings Investments as a trusted name in the industry.</p>
    <p><strong>New Zealand's property market has been experiencing steady growth over the years, making it an attractive destination for property investors.</strong></p>
    <p>With its beautiful landscapes and strong economy, New Zealand offers a diverse range of investment opportunities for both local and international investors. The demand for quality properties in prime locations continues to rise, creating a favorable environment for property investment companies like ours that can lean on our modular benefits of being able to reach unique and remote locations.</p>
  </div>
  <div class="pattern" style="left:981px;top:0;width:129px;height:212px" role="img" aria-label="Light grey geometric line pattern"></div>
  <div class="frame" style="left:794px;top:25px;width:301px;height:322px"></div>
  <div class="photo" style="left:813px;top:51px;width:261px;height:282px;background:linear-gradient(180deg,#e8ecee 0%,#6f7f62 25%,#1c1c1c 45%,#262626 70%,#8a8d88 85%,#c9cbc8 100%)" role="img" aria-label="Black timber modular home with courtyard among trees and hills"></div>
  <div class="footer" style="left:582px;width:504px">www.kestreldwellings.co.nz<span class="rule"></span><span class="folio">4</span></div>
</section>

</body>
</html>
```